Website for Excavator and Earthworks Company

We require a modern, sleek and practical website for our newly created earthworks/excavator business in Perth, Western Australia called Bluegum Ridge Earthworks.

The website should have a modern, cutting edge feel but only needs to be relatively simplistic in it's layout and eventual functionality.

Some pages it should have would be Home, About, Projects and Contact Us.

```html
<!DOCTYPE html>
<html lang="en">
<head>
<meta charset="utf-8">
<title>Bluegum Ridge Earthworks</title>
<link href="https://fonts.googleapis.com/css2?family=Rubik:wght@400;500;700;800&display=swap" rel="stylesheet">
<style>
:root{
  --lime:#cddc00;
  --ink:#1c1c1c;
  --dark:#232323;
  --text:#555a66;
  --white:#ffffff;
}
*{box-sizing:border-box;margin:0;padding:0}
html,body{width:1200px;height:2528px;overflow:hidden;background:var(--white);font-family:"Rubik",sans-serif;color:var(--ink)}
.page{position:relative;width:1200px;height:2528px;overflow:hidden}
.abs{position:absolute}

/* top bar */
.topbar-left{left:0;top:0;width:505px;height:51px;background:var(--lime);clip-path:polygon(0 0,100% 0,94% 100%,6% 100%)}
.topbar-right{left:694px;top:0;width:506px;height:51px;background:var(--lime);clip-path:polygon(0 0,100% 0,94% 100%,6% 100%)}
.follow{left:111px;top:17px;font-size:14px;display:flex;align-items:center;gap:8px;color:var(--ink)}
.social{width:12px;height:12px;background:var(--ink);border-radius:2px}
.email-top{left:755px;top:17px;font-size:14px;display:flex;align-items:center;gap:14px;white-space:nowrap}
.brand{left:500px;top:30px;width:200px;text-align:center;font-weight:700;font-size:22px;line-height:1.1;color:var(--ink);letter-spacing:.5px}
.brand-mark{display:block;width:26px;height:26px;background:var(--lime);margin:0 auto 12px}
.nav{top:93px;font-size:16px;color:var(--ink);white-space:nowrap}
.nav.active{color:var(--lime);font-weight:500}
.nav-dot{left:111px;top:72px;width:14px;height:12px;background:var(--lime)}
.call-btn{left:870px;top:74px;width:218px;height:42px;background:var(--lime);display:flex;align-items:center;justify-content:center;gap:14px;font-weight:500;font-size:16px;white-space:nowrap}

/* hero */
.hero{left:0;top:130px;width:1200px;height:635px;background:linear-gradient(100deg,#3b2a17 0%,#6e4a1f 35%,#c07d28 55%,#8a5a24 75%,#3a2a1a 100%);clip-path:polygon(0 0,100% 0,100% 100%,0 84%)}
.hero-band{left:0;top:675px;width:1200px;height:90px;background:var(--lime);clip-path:polygon(0 0,58% 55%,0 100%)}
.hero-title{left:111px;top:230px;font-size:54px;font-weight:700;line-height:56px;color:var(--white);letter-spacing:-1px;text-transform:uppercase}
.hero-sub{left:111px;top:466px;font-size:18px;line-height:30px;color:var(--white)}
.btn{background:var(--lime);color:var(--ink);font-weight:500;display:flex;align-items:center;justify-content:center;white-space:nowrap}
.hero-btn{left:111px;top:544px;width:180px;height:46px;font-size:16px}

/* who we are */
.frame{left:220px;top:884px;width:404px;height:320px;border:2px solid var(--lime)}
.block{left:111px;top:1179px;width:149px;height:137px;background:var(--lime)}
.about-photo{left:147px;top:907px;width:453px;height:370px;background:linear-gradient(135deg,#8e97a0 0%,#c9b894 45%,#b89560 100%);box-shadow:0 10px 30px rgba(0,0,0,.15)}
.h2{font-weight:700;color:var(--ink);text-transform:uppercase;letter-spacing:-.5px}
.who-title{left:700px;top:908px;font-size:40px}
.who-text{left:700px;width:388px;font-size:14px;line-height:25.7px;color:var(--text);text-align:justify}
.who-btn{left:700px;top:1224px;width:136px;height:46px;font-size:15px}

/* services */
.services-title{left:0;top:1425px;width:1200px;text-align:center;font-size:42px}
.services-sub{left:290px;top:1475px;width:620px;text-align:center;font-size:17px;line-height:27px;color:var(--text)}
.card{top:1555px;width:228px;height:335px;box-shadow:0 4px 14px rgba(0,0,0,.12);border:3px solid var(--white)}
.card-photo{position:absolute;left:0;top:74px;width:100%;height:calc(100% - 74px)}
.card-head{position:absolute;left:0;top:0;width:100%;height:74px;background:var(--dark);color:var(--white);font-size:16px;text-align:center;padding-top:26px;white-space:nowrap}
.card-icon{position:absolute;left:82px;top:57px;width:60px;height:60px;background:var(--lime)}
.card.active{border-color:var(--lime)}
.card.active .card-head{background:var(--lime);color:#3b3b3b}
.card.active .card-icon{background:var(--dark)}
.services-btn{left:517px;top:1927px;width:168px;height:46px;font-size:15px}

/* footer */
.footer{left:0;top:2063px;width:1200px;height:465px;background:linear-gradient(180deg,#2a2a2a,#1b1b1b)}
.footer-band{left:0;top:2063px;width:1200px;height:88px;background:var(--lime);clip-path:polygon(0 0,55% 40%,0 100%)}
.footer-brand{left:300px;top:2196px;width:600px;text-align:center;color:var(--white);font-weight:700;font-size:28px;line-height:32px;white-space:nowrap}
.footer-mark{display:block;width:56px;height:56px;background:var(--white);margin:0 auto 22px}
.footer-nav{left:0;top:2356px;width:1200px;display:flex;justify-content:center;gap:40px;color:var(--white);font-size:16px}
.contact{top:2401px;height:62px;background:var(--lime);display:flex;align-items:center;gap:16px;padding-left:12px;font-size:15px;line-height:22px;color:var(--ink);white-space:nowrap}
.contact-icon{width:40px;height:40px;background:var(--dark);display:flex;align-items:center;justify-content:center;flex:none}
.copyright{left:0;top:2487px;width:1200px;text-align:center;color:var(--white);font-size:12px}
</style>
</head>
<body>
<div class="page">

  <header>
    <div class="abs topbar-left"></div>
    <div class="abs topbar-right"></div>
    <div class="abs follow">FOLLOW US: <span class="social"></span><span class="social"></span><span class="social"></span></div>
    <div class="abs email-top">
      <svg width="14" height="11" viewBox="0 0 14 11"><rect x="0.5" y="0.5" width="13" height="10" fill="none" stroke="#1c1c1c"/><path d="M1 1l6 5 6-5" fill="none" stroke="#1c1c1c"/></svg>
      EMAIL ADDRESS: INFO@BLUEGUMRIDGE.COM.AU
    </div>
    <div class="abs brand"><span class="brand-mark"></span>Bluegum Ridge Earthworks</div>
    <div class="abs nav-dot"></div>
    <div class="abs nav active" style="left:110px">HOME</div>
    <div class="abs nav" style="left:204px">About Bluegum Ridge</div>
    <div class="abs nav" style="left:389px">Projects</div>
    <div class="abs nav" style="left:758px;top:87px">Contact Us</div>
    <div class="abs call-btn">
      <svg width="14" height="14" viewBox="0 0 24 24"><path d="M6.6 10.8a15 15 0 006.6 6.6l2.2-2.2c.3-.3.7-.4 1-.2 1.1.4 2.3.6 3.6.6.6 0 1 .4 1 1V20c0 .6-.4 1-1 1A17 17 0 013 4c0-.6.4-1 1-1h3.5c.6 0 1 .4 1 1 0 1.200.2 2.4.6 3.6.1.3 0 .7-.2 1z" fill="#1c1c1c"/></svg>
      +61 8 5550 1234
    </div>
  </header>

  <section>
    <div class="abs hero" role="img" aria-label="Excavator digging soil at a dusty construction site at sunset"></div>
    <div class="abs hero-band"></div>
    <h1 class="abs hero-title">Raising the<br>groundwork<br>for what comes<br>next</h1>
    <p class="abs hero-sub">Professional Earthworks &amp; Excavation Services<br>Across Perth, Western Australia</p>
    <div class="abs btn hero-btn">View Our Projects</div>
  </section>

  <section>
    <div class="abs frame"></div>
    <div class="abs block"></div>
    <div class="abs about-photo" role="img" aria-label="Site surveyor with tripod and radio beside an excavator on a residential build"></div>
    <h2 class="abs h2 who-title">Who we are</h2>
    <p class="abs who-text" style="top:970px">Sed ut perspiciatis unde omnis iste natus error sit voluptatem accusantium doloremque laudantium, totam rem aperiam, eaque ipsa quae ab illo inventore veritatis et quasi architecto beatae vitae dicta sunt explicabo.</p>
    <p class="abs who-text" style="top:1099px">Nemo enim ipsam voluptatem quia voluptas sit aspernatur aut odit aut fugit, sed quia consequuntur magni dolores eos qui ratione voluptatem sequi nesciunt. Neque porro quisquam est, qui dolorem ipsum</p>
    <div class="abs btn who-btn">Explore More</div>
  </section>

  <section>
    <h2 class="abs h2 services-title">Our Earthworks Services</h2>
    <p class="abs services-sub">Comprehensive excavation and earthmoving services tailored to your project requirements.</p>

    <div class="abs card" style="left:111px">
      <div class="card-photo" role="img" aria-label="Loader filling a dump truck" style="background:linear-gradient(160deg,#6b5a44,#c9873a 55%,#3a2e22)"></div>
      <div class="card-head">Excavation &amp; Earthmoving</div>
      <div class="card-icon"></div>
    </div>
    <div class="abs card" style="left:360px">
      <div class="card-photo" role="img" aria-label="Mini excavator clearing a building lot" style="background:linear-gradient(170deg,#3f5a2e,#8e7a58 55%,#6b5a44)"></div>
      <div class="card-head">Land Clearing &amp; Levelling</div>
      <div class="card-icon"></div>
    </div>
    <div class="abs card active" style="left:609px">
      <div class="card-photo" role="img" aria-label="Paved brick driveway" style="background:linear-gradient(180deg,#8f9488,#c9c6c0 40%,#a9a6a2)"></div>
      <div class="card-head">Driveways &amp; Hardstands</div>
      <div class="card-icon"></div>
    </div>
    <div class="abs card" style="left:858px">
      <div class="card-photo" role="img" aria-label="Concrete drainage pipes on a site" style="background:linear-gradient(170deg,#8a8c8e,#b9bcbf 50%,#9b7d5a)"></div>
      <div class="card-head">Drainage Works</div>
      <div class="card-icon"></div>
    </div>

    <div class="abs btn services-btn">View Full Services</div>
  </section>

  <footer>
    <div class="abs footer" role="img" aria-label="Dark backdrop of excavation works"></div>
    <div class="abs footer-band"></div>
    <div class="abs footer-brand"><span class="footer-mark"></span>Bluegum Ridge Earthworks</div>
    <nav class="abs footer-nav">
      <span>HOME</span><span>|</span><span>ABOUT US</span><span>|</span><span>PROJECTS</span><span>|</span><span>CONTACT US.</span>
    </nav>
    <div class="abs contact" style="left:198px;width:270px">
      <div class="contact-icon"><svg width="18" height="20" viewBox="0 0 24 24"><path d="M12 2a7 7 0 00-7 7c0 5 7 13 7 13s7-8 7-13a7 7 0 00-7-7zm0 9.5A2.5 2.5 0 1112 6.5a2.5 2.5 0 010 5z" fill="#cddc00"/></svg></div>
      <div>Bluegum Ridge Earthworks,<br>Western Australia</div>
    </div>
    <div class="abs contact" style="left:498px;width:213px">
      <div class="contact-icon"><svg width="18" height="18" viewBox="0 0 24 24"><path d="M6.6 10.8a15 15 0 006.6 6.6l2.2-2.2c.3-.3.7-.4 1-.2 1.1.4 2.3.6 3.6.6.6 0 1 .4 1 1V20c0 .6-.4 1-1 1A17 17 0 013 4c0-.6.4-1 1-1h3.5c.6 0 1 .4 1 1 0 1.2.2 2.4.6 3.6.1.3 0 .7-.2 1z" fill="#cddc00"/></svg></div>
      <div>Call Us:<br>+61 8 5550 1234</div>
    </div>
    <div class="abs contact" style="left:741px;width:262px">
      <div class="contact-icon"><svg width="20" height="15" viewBox="0 0 20 15"><rect x="1" y="1" width="18" height="13" fill="none" stroke="#cddc00" stroke-width="2"/><path d="M1 1l9 7 9-7" fill="none" stroke="#cddc00" stroke-width="2"/></svg></div>
      <div>Email Us:<br>info@bluegumridge.com.au</div>
    </div>
    <p class="abs copyright">(C) Copyright 2026 | All Rights Reserved</p>
  </footer>

</div>
</body>
</html>
```